Brivolt Technologies business card design

We need a business card designed with our new logo. it would be great if the card could communicate it is a technology based company.

Target Market(s)

system integrators

Industry/Entity Type

technology, IOT

Contact Information for Business Card

Name, designation, Address, telephone number, email address

Requirements
Must have
• logo and company name
Nice to have
• something to do with technology

```html
<!DOCTYPE html>
<html lang="en">
<head>
<meta charset="utf-8">
<title>Brivolt Technologies – Business Card</title>
<link rel="stylesheet" href="https://fonts.googleapis.com/css2?family=Montserrat:wght@400;500;700&display=swap">
<style>
  :root {
    --page-bg: #1e1e1e;
    --card-dark: #3e3e3e;
    --card-light: #ffffff;
    --accent: #f7931e;
    --text-light: #f2f2f2;
    --map-tone: #4a4a4a;
  }
  * { box-sizing: border-box; margin: 0; padding: 0; }
  html, body {
    width: 1200px; height: 900px; overflow: hidden;
    background: var(--page-bg);
    font-family: "Montserrat", Arial, sans-serif;
  }
  .sheet {
    width: 1200px; height: 900px;
    display: flex; flex-direction: column; align-items: center; justify-content: center;
    gap: 30px;
  }
  .card {
    position: relative; width: 700px; height: 400px;
    border-radius: 22px; overflow: hidden;
    box-shadow: 0 10px 24px rgba(0,0,0,.45);
  }
  .card-front { background: var(--card-light); }
  .card-front .wave { position: absolute; inset: 0; width: 100%; height: 100%; }
  .wave-dark { fill: var(--card-dark); }
  .wave-stripe { fill: none; stroke: var(--accent); stroke-width: 7; stroke-linecap: round; }

  .contact {
    position: absolute; left: 38px; top: 132px;
    color: var(--text-light); font-size: 15px; line-height: 1.45;
  }
  .contact .name {
    color: var(--accent); font-weight: 700; font-size: 21px;
    letter-spacing: .3px; text-transform: uppercase; margin-bottom: 2px;
  }
  .contact .role { margin-bottom: 8px; }
  .contact .address { margin-bottom: 8px; }
  .contact-line { display: flex; align-items: center; gap: 10px; }
  .contact-line svg { width: 15px; height: 15px; flex: none; }
  .icon { fill: none; stroke: var(--accent); stroke-width: 2; stroke-linecap: round; stroke-linejoin: round; }

  .front-brand {
    position: absolute; right: 32px; top: 228px;
    display: flex; align-items: center; gap: 10px;
  }
  .brand-mark { width: 16px; height: 16px; background: var(--accent); }
  .brand-name {
    font-weight: 700; font-size: 25px; color: var(--card-dark); letter-spacing: .3px;
    white-space: nowrap;
  }

  .card-back { background: var(--card-dark); }
  .world-map {
    position: absolute; left: 70px; top: 40px; width: 560px; height: 320px;
    border-radius: 40px;
    background: radial-gradient(ellipse at center, var(--map-tone) 0%, rgba(74,74,74,.5) 55%, rgba(62,62,62,0) 80%);
  }
  .back-brand {
    position: absolute; inset: 0;
    display: flex; align-items: center; justify-content: center;
  }
  .back-brand .brand-name { color: var(--text-light); font-size: 40px; }
</style>
</head>
<body>
<main class="sheet">
  <section class="card card-front" aria-label="Business card front">
    <svg class="wave" viewBox="0 0 700 400" preserveAspectRatio="none" aria-hidden="true">
      <path class="wave-dark" d="M0,400 V100 C130,55 230,70 290,180 S430,390 640,400 Z"/>
      <path class="wave-stripe" d="M95,66 C185,52 250,80 305,172 S455,378 660,386"/>
    </svg>

    <div class="contact">
      <p class="name">Dalen Corvish</p>
      <p class="role">Co-Founder</p>
      <p class="address">Harlow Point 2810 Vale<br>Crossing Suite 114</p>
      <p class="contact-line">
        <svg viewBox="0 0 16 16" aria-hidden="true"><path class="icon" d="M4 2l2.5 3-1.5 1.5a8 8 0 0 0 4.5 4.5L11 9.5l3 2.5-1.5 2A10 10 0 0 1 2 3.5z"/></svg>
        <span>555-014-2270</span>
      </p>
      <p class="contact-line">
        <svg viewBox="0 0 16 16" aria-hidden="true"><rect class="icon" x="1.5" y="3.5" width="13" height="9"/><path class="icon" d="M1.5 3.5l6.5 5 6.5-5"/></svg>
        <span>info@brivolttech.com</span>
      </p>
      <p class="contact-line">
        <svg viewBox="0 0 16 16" aria-hidden="true"><circle class="icon" cx="8" cy="8" r="6.5"/><path class="icon" d="M1.5 8h13M8 1.5c2.5 2.5 2.5 10.5 0 13M8 1.5c-2.5 2.5-2.5 10.5 0 13"/></svg>
        <span>www.brivolttech.com</span>
      </p>
    </div>

    <div class="front-brand">
      <span class="brand-mark" aria-hidden="true"></span>
      <span class="brand-name">Brivolt Technologies</span>
    </div>
  </section>

  <section class="card card-back" aria-label="Business card back">
    <div class="world-map" role="img" aria-label="Faint dotted world map in the background"></div>
    <div class="back-brand">
      <span class="brand-name">Brivolt Technologies</span>
    </div>
  </section>
</main>
</body>
</html>
```